Thornbury Building Company - Card Design

I am looking to use the logo designs that you already did for me to develop a business card. I would like the card to have a black background and be double sided. I want white and green logo and text. I have attached an inspiration photo of a look that I like. I would like to use the Vertical Logo attached to take up the full front side of the card. On the back where I have my name and information, I would like to have the horizontal logo or maybe even just the image of the 'A' and trees without the text. I am open, but I am looking for something clean and simple and I want the green to really pop! Additional files can be found under Design #: 58302946

Target Market(s)

Homeowners

Industry/Entity Type

Construction

Contact Information for Business Card

Name: Marcus Thornbury, Title: Project Manager, Phone: 555.274.8136, Email: thornburybuildingcompany@mailvesta.com, address: 487 Larkspur Ln, Alder Ridge, OR 95033, Lic# 2468317

Colors
00AB8E
00BBA5
67D7C9
C6EFE9
E9F9F6

Requirements
Nice to have
• I would like to see the logos that I have already got from ArtLoomHub, though I am open to new ones

```html
<!DOCTYPE html>
<html lang="en">
<head>
<meta charset="utf-8">
<title>Thornbury Building Company – Business Card</title>
<link href="https://fonts.googleapis.com/css2?family=Arimo:wght@400;700&display=swap" rel="stylesheet">
<style>
  :root {
    --backdrop: #c9c9c9;
    --card: #1d1d1d;
    --card-deep: #141414;
    --green: #6abf45;
    --white: #ffffff;
    --text-soft: #e8e8e8;
  }
  * { box-sizing: border-box; margin: 0; padding: 0; }
  html, body { width: 1200px; height: 788px; overflow: hidden; }
  body {
    background: var(--backdrop);
    font-family: "Arimo", Arial, sans-serif;
    display: flex;
    align-items: center;
    justify-content: center;
    gap: 56px;
  }
  .card {
    position: relative;
    width: 532px;
    height: 304px;
    border-radius: 24px;
    background: linear-gradient(160deg, var(--card) 0%, var(--card-deep) 100%);
    border-bottom: 4px solid var(--green);
    overflow: hidden;
    flex: none;
  }

  /* Info side */
  .card-info { padding: 36px 40px; }
  .card-info .edge-tab {
    position: absolute;
    left: 0; top: 150px;
    width: 8px; height: 34px;
    background: var(--green);
  }
  .brand {
    display: flex;
    align-items: center;
    gap: 10px;
    white-space: nowrap;
  }
  .brand-square {
    width: 18px; height: 18px;
    background: var(--green);
    flex: none;
  }
  .brand-name {
    font-weight: 700;
    font-size: 19px;
    letter-spacing: 1.5px;
    text-transform: uppercase;
    color: var(--white);
  }
  .person { margin-top: 30px; }
  .person-name {
    font-weight: 700;
    font-size: 22px;
    letter-spacing: 1px;
    text-transform: uppercase;
    color: var(--green);
  }
  .person-title {
    font-size: 13px;
    color: var(--text-soft);
    margin-top: 3px;
  }
  .details { margin-top: 18px; font-size: 13px; color: var(--text-soft); line-height: 1.5; }
  .licence { color: var(--green); }
  .contact { margin-top: 12px; display: grid; gap: 5px; }
  .contact-row { display: flex; align-items: center; gap: 9px; }
  .contact-row svg { width: 13px; height: 13px; fill: var(--green); flex: none; }

  /* Logo side */
  .card-logo {
    display: flex;
    align-items: center;
    justify-content: center;
    padding: 0 32px;
  }
  .card-logo .brand { gap: 14px; }
  .card-logo .brand-square { width: 24px; height: 24px; }
  .card-logo .brand-name { font-size: 22px; letter-spacing: 1.5px; }
</style>
</head>
<body>
  <section class="card card-info">
    <span class="edge-tab"></span>
    <div class="brand">
      <span class="brand-square"></span>
      <span class="brand-name">Thornbury Building Company</span>
    </div>
    <div class="person">
      <p class="person-name">Marcus Thornbury</p>
      <p class="person-title">Project Manager</p>
    </div>
    <div class="details">
      <p class="licence">Lic# 2468317</p>
      <p class="address">487 Larkspur Ln, Alder Ridge, OR 95033</p>
      <div class="contact">
        <p class="contact-row">
          <svg viewBox="0 0 24 24" aria-hidden="true"><path d="M6.6 10.8a15.1 15.1 0 0 0 6.6 6.6l2.2-2.2a1 1 0 0 1 1-.25 11.4 11.4 0 0 0 3.6.57 1 1 0 0 1 1 1V20a1 1 0 0 1-1 1A17 17 0 0 1 3 4a1 1 0 0 1 1-1h3.5a1 1 0 0 1 1 1c0 1.250.2 2.450.57 3.570a1 1 0 0 1-.25 1z"/></svg>
          <span>555.274.8136</span>
        </p>
        <p class="contact-row">
          <svg viewBox="0 0 24 24" aria-hidden="true"><path d="M2 5h20v14H2zm2 2v.5l8 5 8-5V7l-8 5z"/></svg>
          <span>thornburybuildingcompany@mailvesta.com</span>
        </p>
      </div>
    </div>
  </section>

  <section class="card card-logo">
    <div class="brand">
      <span class="brand-square"></span>
      <span class="brand-name">Thornbury Building Company</span>
    </div>
  </section>
</body>
</html>
```